This book will apply the 12 Steps to gaming addiction, also known as video game addiction. The primary purpose of the book is to provide an effective solution for this new type of addiction. The solution is based on the rich and successful concepts of traditional twelve-step programs like RQ.

The title on the cover will be "Nine Doors Out of the Endless Level" and "by Peter Halvorn". A subtitle can be used if it works in your design of "A Practical Path Back from Compulsive Screen Play". Cover will be for a 6" x 9" book approximately 110 pages in length.

Some back cover text including some review quotes and an author bio are in the attached Word doc. There is also an author photo attached for for the back cover.

Requirements
Must have
• For the cover design it could be stylized, or an image, a partial image, or whatever. I am open to suggestions. Think about what would be noticed by a person searching for help with moderating their video game use, or by the parents or loved ones of problem gamers. Something contemporary and eye catching.

```html
<!DOCTYPE html>
<html lang="en">
<head>
<meta charset="utf-8">
<title>Nine Doors Out of the Endless Level – Back Cover</title>
<link href="https://fonts.googleapis.com/css2?family=Barlow+Condensed:wght@300;400;500;600&family=Oswald:wght@500&family=Silkscreen&display=swap" rel="stylesheet">
<style>
  :root {
    --bg: #050509;
    --panel: rgba(6, 6, 12, 0.88);
    --ink: #f2f2f6;
    --lavender: #c6c9f0;
    --accent: #ff4a2a;
    --rule: #d8d8e0;
    --glow-blue: #2a3b8f;
    --glow-red: #7a2038;
  }
  * { margin: 0; padding: 0; box-sizing: border-box; }
  html, body { width: 800px; height: 1200px; overflow: hidden; background: var(--bg); }
  .back-cover {
    position: relative;
    width: 800px;
    height: 1200px;
    overflow: hidden;
    background: var(--bg);
    font-family: "Barlow Condensed", sans-serif;
    font-weight: 300;
    color: var(--ink);
  }
  .backdrop {
    position: absolute;
    inset: 0;
    background:
      radial-gradient(ellipse 220px 300px at 120px 180px, rgba(90, 60, 130, 0.55), transparent 70%),
      radial-gradient(ellipse 260px 420px at 560px 420px, rgba(42, 59, 143, 0.55), transparent 70%),
      radial-gradient(ellipse 180px 260px at 40px 420px, rgba(122, 32, 56, 0.45), transparent 70%),
      radial-gradient(ellipse 300px 200px at 80px 1100px, rgba(60, 60, 110, 0.35), transparent 70%),
      linear-gradient(180deg, #0b0a16 0%, #07070e 60%, #040406 100%);
  }
  .praise-panel {
    position: absolute;
    left: 106px;
    top: 102px;
    width: 278px;
    height: 1010px;
    background: var(--panel);
    padding: 26px 18px 0 17px;
  }
  .praise-heading { text-align: center; margin-bottom: 18px; }
  .praise-heading .lead {
    display: block;
    font-family: "Barlow Condensed", sans-serif;
    font-weight: 500;
    font-size: 30px;
    line-height: 1;
    color: var(--lavender);
    letter-spacing: 0.5px;
  }
  .praise-heading .pixel {
    display: block;
    font-family: "Silkscreen", monospace;
    font-size: 15px;
    line-height: 1;
    margin-top: 6px;
    color: var(--lavender);
    letter-spacing: 0.5px;
  }
  .praise-heading .title {
    display: block;
    font-family: "Oswald", sans-serif;
    font-weight: 500;
    font-size: 40px;
    line-height: 0.98;
    margin-top: 4px;
    color: var(--accent);
    text-transform: uppercase;
  }
  .review p {
    font-size: 15.5px;
    line-height: 21.4px;
    text-align: justify;
  }
  .review .credit {
    text-align: right;
    margin-top: 10px;
    font-size: 13.5px;
    line-height: 17px;
  }
  .review .credit strong { font-weight: 600; color: var(--lavender); display: block; }
  .divider {
    width: 185px;
    height: 1px;
    background: var(--rule);
    margin: 32px auto 28px;
  }
  .blurb {
    position: absolute;
    left: 410px;
    top: 118px;
    width: 298px;
    font-size: 15.5px;
    line-height: 21.4px;
  }
  .blurb p + p { margin-top: 21px; }
  .blurb .divider { width: 230px; margin: 20px 0 22px 4px; }
  .about-heading {
    font-weight: 500;
    font-size: 25px;
    line-height: 1;
    color: var(--lavender);
    margin: 0 0 12px 2px;
  }
  .author-photo {
    float: left;
    width: 171px;
    height: 190px;
    margin: 2px 10px 4px 2px;
    border-radius: 10px;
    background: linear-gradient(160deg, #7a8a4a 0%, #4e5a3a 45%, #1b1f2a 100%);
  }
</style>
</head>
<body>
<div class="back-cover">
  <div class="backdrop" role="img" aria-label="Blurred dark background of a gamer wearing a headset, lit in blue and red with digital glitch streaks"></div>

  <aside class="praise-panel">
    <h2 class="praise-heading">
      <span class="lead">PRAISE FOR</span>
      <span class="pixel">NINE DOORS OUT OF</span>
      <span class="title">The Endless<br>Level</span>
    </h2>

    <blockquote class="review">
      <p>“A must-read for anyone who is addicted to or thinks they may have a problem with digital gaming. This eloquent work will also be useful to academics and clinicians exploring potential solutions. The author recognizes the similarities between gaming addiction and other addictions, and logically applies one of the most effective known solutions for addiction - The Twelve Steps.”</p>
      <div class="credit"><strong>- Dale Ridgemont</strong>Noted Interventionist and Keynote Speaker</div>
    </blockquote>

    <div class="divider"></div>

    <blockquote class="review">
      <p>“If you suffer from digital gaming addiction, I strongly encourage you to use this book as your road map to get you back to the real world.”</p>
      <div class="credit"><strong>- Connor Bayliss</strong>Founder of Signal Feed Weekly.</div>
    </blockquote>

    <div class="divider"></div>

    <blockquote class="review">
      <p>“As a high school teacher for 24 years, husband, father, coach, and 12-Step member, I can assure you that this book will transform the life of anyone who is addicted to video games. Well written, easy to understand, and a wonderful book that will provide you with a clear road map to recovery, and this includes teenagers, a group I have been working with in the classroom for decades.”</p>
      <div class="credit"><strong>- Luis Ortega</strong>Harbor Point High School Teacher.</div>
    </blockquote>
  </aside>

  <section class="blurb">
    <p>A Practical Path Back from Compulsive Screen Play (aka Video Game Addiction) based on the rich and successful tradition of the Twelve Steps.</p>
    <p>Addiction to Digital Gaming is a new and troubling phenomenon that has burst upon an unprepared society with alarming speed. Many people crave the use of Digital Games in a strikingly similar way to any other addict. Digital Games are a complex software and hardware system that have been designed to promote continued and progressive usage. This sophisticated technology clearly feeds on natural addictive tendencies.</p>
    <p>The 12 Steps are one of the most effective methods for treating addiction in human history. Originating with Recovery Quorum (RQ) in 1939, the 12 Steps have since been used to treat a variety of other addictions, including drugs, sex, gambling, eating disorders, and many others. Now in this groundbreaking work the 12 Steps are applied to the complex and evolving contemporary phenomenon of Digital Gaming Addiction.</p>

    <div class="divider"></div>

    <h3 class="about-heading">About the Author</h3>
    <div class="author-photo" role="img" aria-label="Portrait photo of the author in a dark blazer against leafy green background"></div>
    <p>Peter Halvorn is a Technology Consultant and Writer with many years of professional coding and consulting experience. He also struggled with addiction to drugs and alcohol and is now clean and sober in a Twelve-Step program for over 17 years. This unique combination of 12-Step experience and technology expertise led him to create Nine Doors Out of the Endless Level.</p>
  </section>
</div>
</body>
</html>
```